Responsive Software/Service company website

I need a complete, responsive, company website design (Wordpress).
A short intro to what we do:
Brindlecore is a Danish software company specialized in Zentrova Ledger KEX for SMB clients in Europe.
We deliver POS and ERP systems to retail shops and entertainment business.
Besides this, we offer tight integration to eCommerce solutions.
For eCommerce we have 2 products, both heavily customized for a tight integration.
B2C (Quillora) and B2B
For both eCommerce and KEX solutions we have several sub groups, modules and specifications.
Our target group is existing (looking for eCommerce) and new retailers (looking for POS and eCommerce)
I'm looking for a clean way to promote our products in an easily accessible way.
As well as having a section for more detailed information on each product.
I have uploaded a wire frame suggestion. Please do not take it too literally. You have absolutely creative freedom if you have a better, more creative idea.
See it as an inspiration as to what elements we would like on the site (not necessarily on the front page)
Feel free to use/suggest Stock photos. We are aware that prices of those come on top. We also have pro photographer+studio available if you have any suggestions that requires that.
Updates
Hi all
Target Market(s)
European retailers/shop owners.
Either looking for a POS / ERP system or looking for eCommerce integration to their existing ZL KEX system.
Industry/Entity Type
Entertainment
Requirements
Must have
- The logo I uploaded has to be part of it. Can't be changed.
Same goes for colours
Must be responsive to work on mobile and desktop. Final design PSDs must reflect this and show how it would look on both platforms.
Final PSds must also show examples of any interaction like mouseover, colour changes, image change or dynamics.
Nice to have
- Custom made icons to accompany(replace?) text links are a very big plus.
Custom made icons/logo for each sub product (see wire frame bottom) :
BC Retail
BC Entertainment
BC Ticketing
BC Webshop
etc
for easily distinction would be a big plus too.
The use of "hand drawn" elements mixed with straight, minimalistic design, like here on ArtHarbor, can be used.
Should not have
- This is the existing site I'm looking to change away from:
http://www.brindlecore.example/ (in danish)
Too much info, too cramped, not nice looking and generally not very user friendly imo.

```html
<!DOCTYPE html>
<html lang="da">
<head>
<meta charset="utf-8">
<title>Brindlecore – POS, ERP og webshop til Zentrova Ledger KEX</title>
<link rel="stylesheet" href="https://fonts.googleapis.com/css2?family=Arimo:wght@400;700&display=swap">
<style>
:root{
  --bg:#ececec;
  --white:#ffffff;
  --brand:#0b5aa8;
  --brand-hero:#0f62b4;
  --brand-deep:#0a3f7a;
  --navy:#0b4a8c;
  --cyan:#5bc3da;
  --dark:#2c2d30;
  --footer:#1e1f21;
  --footer-text:#a9abae;
  --text:#2b2b2b;
  --muted:#555;
  --line:#d2d2d2;
  --news-blue:#6aa3d8;
}
*{box-sizing:border-box;margin:0;padding:0}
html,body{width:1200px;height:3403px;overflow:hidden;background:var(--bg);font-family:"Arimo",Arial,sans-serif;color:var(--text)}
.page{position:absolute;left:91px;top:95px;width:1032px;height:3308px;background:var(--white);overflow:hidden}
.abs{position:absolute}

.top-strip{left:0;top:0;width:100%;height:14px;background:var(--brand)}
.site-header{left:0;top:14px;width:100%;height:156px}
.logo{position:absolute;left:14px;top:50px;font-size:62px;font-weight:700;letter-spacing:3px;color:var(--brand)}
.home-link{position:absolute;left:736px;top:56px;width:66px;height:66px}
.menu-button{position:absolute;left:835px;top:63px;width:172px;height:61px;background:var(--navy);border:3px solid #7fb2e0;color:#fff;font-size:32px;display:flex;align-items:center;justify-content:center;gap:14px}

.hero{left:0;top:170px;width:100%;height:522px;background:linear-gradient(120deg,#0c57a4,var(--brand-hero) 55%,#1a6fc0)}
.hero-title{position:absolute;left:103px;top:150px;width:620px;color:#fff;font-size:39px;line-height:50px;font-weight:400}
.hero-visual{position:absolute;left:620px;top:30px;width:412px;height:440px;background:radial-gradient(ellipse at 60% 50%,#e8eef4 0%,#a9bfd6 35%,rgba(15,98,180,0) 70%)}
.hero-arrow{position:absolute;top:225px;width:40px;height:64px}
.hero-dots{position:absolute;left:455px;top:484px;display:flex;gap:8px}
.hero-dots span{width:18px;height:18px;border-radius:50%;background:#fff}
.hero-dots span:first-child{background:#8fb5dc}

.intro-bar{left:0;top:692px;width:100%;height:111px;background:var(--dark);color:#fff}
.intro-bar p{position:absolute;left:20px;top:22px;width:680px;font-size:25px;font-weight:700;line-height:33px}
.agent-visual{position:absolute;left:735px;top:10px;width:80px;height:101px;background:linear-gradient(#c86a3a,#3b3d44);border-radius:40px 40px 0 0}
.contact-lines{position:absolute;left:826px;top:22px;font-size:24px;line-height:36px}
.contact-lines .small{font-size:12px}
.contact-lines div{display:flex;align-items:center;gap:10px;white-space:nowrap}

.solution-card{top:833px;width:322px;height:311px;border:2px solid var(--line);text-align:center;box-shadow:0 2px 4px rgba(0,0,0,.15)}
.solution-card .icon{width:84px;height:74px;margin:22px auto 0;border-radius:6px}
.solution-card h3{color:var(--brand);font-size:38px;font-weight:400;margin-top:20px}
.solution-card p{font-size:32px;line-height:38px;margin-top:12px}
.read-more{display:flex;height:39px;width:195px;font-size:20px;color:#fff;font-weight:700}
.read-more span{flex:1;background:var(--navy);display:flex;align-items:center;padding-left:20px}
.read-more i{width:34px;background:var(--cyan);display:flex;align-items:center;justify-content:center}

.divider{left:0;top:1217px;width:100%;height:11px;background:#d3d3d3}

.panel{left:125px;width:774px;border:2px solid var(--line);box-shadow:0 2px 4px rgba(0,0,0,.15)}
.panel h2{position:absolute;left:38px;top:14px;color:var(--brand);font-size:38px;font-weight:700}
.panel .rule{position:absolute;left:38px;top:68px;width:222px;height:6px;background:#9a9a9a;border-radius:3px}
.panel .rule::before{content:"";position:absolute;left:-4px;top:-4px;width:14px;height:14px;border-radius:50%;background:#9a9a9a}

.customers{top:1245px;height:343px}
.customers .label{position:absolute;left:55px;top:90px;font-size:25px}
.customers .lead{position:absolute;left:55px;top:128px;font-size:23px;color:var(--muted)}
.partner-grid{position:absolute;left:130px;top:172px;display:grid;grid-template-columns:repeat(3,148px);gap:14px 20px}
.partner-grid span{height:60px;border:2px solid #e1e1e1;display:flex;align-items:center;justify-content:center;font-size:24px;font-weight:700;color:var(--brand-deep)}

.news{top:1664px;height:488px}
.news-item{position:absolute;left:0;width:100%;padding:0 36px 0 55px}
.news-item + .news-item{border-top:2px solid var(--line)}
.news-item h4{font-size:25px;font-weight:400;line-height:25px;margin-bottom:12px}
.news-item p{font-size:18px;line-height:22px;color:#444;width:640px}
.news-item .more{text-align:right;font-size:18px;line-height:22px;color:var(--brand);margin-top:6px}
.date-badge{position:absolute;right:36px;width:46px;background:var(--navy);color:#fff;font-size:15px;text-align:center;line-height:26px}
.date-badge b{display:block;font-weight:400;background:var(--dark)}

.hotline{top:2213px;height:463px}
.hotline .body{position:absolute;left:40px;top:95px;width:690px}
.hotline h4{font-size:25px;font-weight:400;margin-bottom:8px}
.hotline p{font-size:20px;line-height:25px;color:#444}
.hotline h5{font-size:25px;font-weight:400;margin:22px 0 14px}
.hotline li{list-style:none;font-size:20px;color:#444;margin-bottom:28px}

.newsletter{left:0;top:2733px;width:100%;height:89px;background:var(--news-blue);color:#fff}
.newsletter h3{position:absolute;left:9px;top:28px;font-size:31px;font-weight:400}
.newsletter p{position:absolute;left:196px;top:20px;width:320px;font-size:12px;line-height:15px}
.newsletter .field{position:absolute;left:545px;top:22px;width:305px;height:48px;background:#fff;border:2px solid #3d75b0}
.newsletter .submit{position:absolute;left:873px;top:18px;width:154px;height:57px;background:var(--navy);font-size:25px;font-weight:700;display:flex;align-items:center;justify-content:center}

.address-bar{left:0;top:2833px;width:100%;height:79px;background:#f6f6f6;display:flex;align-items:center;padding-left:14px;font-size:15px;gap:8px}
.social{position:absolute;right:28px;top:20px;display:flex;gap:8px}
.social span{width:36px;height:36px;background:var(--navy)}

.site-footer{left:0;top:2912px;width:100%;height:396px;background:var(--footer)}
.footer-col{position:absolute;top:14px}
.footer-col h4{color:var(--brand);font-size:20px;font-weight:400;line-height:24px;margin-bottom:14px}
.footer-col li{list-style:none;color:var(--footer-text);font-size:15px;line-height:36px;white-space:nowrap}
.footer-col.compact li{line-height:33px}
.badge{position:absolute;left:808px;width:130px;height:52px;border-radius:3px}
</style>
</head>
<body>
<div class="page">
  <div class="abs top-strip"></div>

  <header class="abs site-header">
    <div class="logo">BRINDLECORE</div>
    <svg class="home-link" viewBox="0 0 66 66" aria-label="Forside">
      <path d="M33 6 L4 32 h9 v28 h15 V42 h10 v18 h15 V32 h9 z" fill="var(--brand)"/>
    </svg>
    <div class="menu-button">Menu
      <svg width="40" height="32" viewBox="0 0 40 32"><rect y="0" width="40" height="6" fill="#fff"/><rect y="13" width="40" height="6" fill="#fff"/><rect y="26" width="40" height="6" fill="#fff"/></svg>
    </div>
  </header>

  <section class="abs hero">
    <div class="hero-visual" role="img" aria-label="Foto af slebne diamanter"></div>
    <h1 class="hero-title">BC Jewellery – brancheløsning<br>til guldsmede</h1>
    <svg class="hero-arrow" style="left:8px" viewBox="0 0 40 64"><path d="M32 4 L8 32 L32 60" stroke="#fff" stroke-width="10" fill="none"/></svg>
    <svg class="hero-arrow" style="left:984px" viewBox="0 0 40 64"><path d="M8 4 L32 32 L8 60" stroke="#fff" stroke-width="10" fill="none"/></svg>
    <div class="hero-dots"><span></span><span></span><span></span><span></span></div>
  </section>

  <section class="abs intro-bar">
    <p>Brindlecore supplies cash register systems and ticketing solutions based on Zentrova Ledger KEX.</p>
    <div class="agent-visual" role="img" aria-label="Illustration af kundeservicemedarbejder med headset"></div>
    <div class="contact-lines">
      <div><svg width="20" height="20" viewBox="0 0 22 22"><circle cx="11" cy="11" r="11" fill="#fff"/><rect x="6" y="7" width="10" height="8" fill="var(--dark)"/></svg>40 11 55 60</div>
      <div class="small"><svg width="20" height="20" viewBox="0 0 22 22"><circle cx="11" cy="11" r="11" fill="#fff"/><rect x="5" y="7" width="12" height="8" fill="var(--dark)"/></svg>retail@brindlecore.example</div>
    </div>
  </section>

  <article class="abs solution-card" style="left:9px">
    <div class="icon" role="img" aria-label="Ikon af butiksfacade" style="background:linear-gradient(#d23a2a,#7a5a44)"></div>
    <h3>Retail</h3><p>Solutions for<br>all industies</p>
  </article>
  <div class="abs read-more" style="left:9px;top:1149px"><span>Read more</span><i><svg width="12" height="16" viewBox="0 0 12 16"><path d="M2 2l7 6-7 6" stroke="#fff" stroke-width="3" fill="none"/></svg></i></div>

  <article class="abs solution-card" style="left:356px">
    <div class="icon" role="img" aria-label="Ikon af indkøbsvogn" style="background:linear-gradient(#c9c9c9,#b53a36)"></div>
    <h3>Webshops</h3><p>E-commerce<br>from KEX</p>
  </article>
  <div class="abs read-more" style="left:356px;top:1149px"><span>Read more</span><i><svg width="12" height="16" viewBox="0 0 12 16"><path d="M2 2l7 6-7 6" stroke="#fff" stroke-width="3" fill="none"/></svg></i></div>

  <article class="abs solution-card" style="left:697px">
    <div class="icon" role="img" aria-label="Ikon af billet og blyant" style="background:linear-gradient(#e6e2d6,#5f8fc4)"></div>
    <h3>Entertainment</h3><p>Cash registers<br>and ticketing</p>
  </article>
  <div class="abs read-more" style="left:697px;top:1149px"><span>Read more</span><i><svg width="12" height="16" viewBox="0 0 12 16"><path d="M2 2l7 6-7 6" stroke="#fff" stroke-width="3" fill="none"/></svg></i></div>

  <div class="abs divider"></div>

  <section class="abs panel customers">
    <h2>Customers</h2><div class="rule"></div>
    <div class="label">Recommondation:</div>
    <div class="lead">Te sinimosa se conseque optatias recus eliquatium hitis audipsus</div>
    <div class="partner-grid">
      <span>Corvane</span><span>Mistral</span><span>Teravo</span>
      <span>Pellux</span><span>Oakrin</span><span>Solvane</span>
    </div>
  </section>
  <div class="abs read-more" style="left:125px;top:1588px"><span>Read more</span><i><svg width="12" height="16" viewBox="0 0 12 16"><path d="M2 2l7 6-7 6" stroke="#fff" stroke-width="3" fill="none"/></svg></i></div>

  <section class="abs panel news">
    <h2>News</h2><div class="rule"></div>
    <div class="news-item" style="top:0;padding-top:112px;height:268px">
      <div class="date-badge" style="top:27px">09<b>Oct</b></div>
      <h4>Newsheader 1</h4>
      <p>Nyhedsbrødtekst Em veleste serore, utam si bera quam quiditi ssimagn atetur, si nullit quunt.Te sinimosa se conseque optatias recus eliquatium hitis audipsus expeles si di oditi bla volorercit id quo cuptatem et mi, nonsed maio ideriatiur? Nem sitecto taquis andae lam</p>
      <div class="more">- Readmore&gt;&gt;</div>
    </div>
    <div class="news-item" style="top:268px;padding-top:46px;height:216px">
      <div class="date-badge" style="top:16px">09<b>Oct</b></div>
      <h4>Newsheader 1</h4>
      <p>Nyhedsbrødtekst Em veleste serore, utam si bera quam quiditi ssimagn atetur, si nullit quunt.Te sinimosa se conseque optatias recus eliquatium hitis audipsus expeles si di oditi bla volorercit id quo cuptatem et mi, nonsed maio ideriatiur? Nem sitecto taquis andae lam</p>
      <div class="more">- Readmore&gt;&gt;</div>
    </div>
  </section>
  <div class="abs read-more" style="left:125px;top:2152px"><span>Read more</span><i><svg width="12" height="16" viewBox="0 0 12 16"><path d="M2 2l7 6-7 6" stroke="#fff" stroke-width="3" fill="none"/></svg></i></div>

  <section class="abs panel hotline">
    <h2>Hotline</h2><div class="rule"></div>
    <div class="body">
      <h4>Call 40 11 55 60, press 2</h4>
      <p>Te sinimosa se conseque optatias recus eliquatium hitis audipsus expeles si di oditi bla volorercit id quo cuptatem et mi. Te sinimosa se conseque optatias recus eliquatium hitis audipsus expeles si di oditi bla volorercit id quo cuptatem et mi. Te hitis audipsus expeles si di oditi bla volorercit id quo cuptatem et mi.</p>
      <h5>Opening hours:</h5>
      <ul><li>Mandag-fredag 08.00-20.00</li><li>Lørdag 09.00-16.00</li><li>Søndag 10.00-16.00</li></ul>
    </div>
  </section>
  <div class="abs read-more" style="left:125px;top:2676px"><span>Read more</span><i><svg width="12" height="16" viewBox="0 0 12 16"><path d="M2 2l7 6-7 6" stroke="#fff" stroke-width="3" fill="none"/></svg></i></div>

  <section class="abs newsletter">
    <h3>Newsletter</h3>
    <p>Em veleste serore, utam si bera quam quiditi ssimagn atetur, si nullit quunt. Te sinimosa se conseque optatias recus.</p>
    <div class="field"></div>
    <div class="submit">Submit</div>
  </section>

  <div class="abs address-bar">
    <svg width="22" height="22" viewBox="0 0 22 22"><circle cx="11" cy="11" r="11" fill="var(--brand-deep)"/><path d="M11 5l-6 6h2v6h8v-6h2z" fill="#fff"/></svg>
    <span>Brindlecore København Vestergade 48 - 2100 København Ø</span>
    <svg width="22" height="22" viewBox="0 0 22 22" style="margin-left:10px"><circle cx="11" cy="11" r="11" fill="var(--brand-deep)"/><rect x="5" y="7" width="12" height="8" fill="#fff"/></svg>
    <span>retail@brindlecore.example</span>
    <div class="social" aria-label="Sociale medier"><span></span><span></span><span></span></div>
  </div>

  <footer class="abs site-footer">
    <div class="footer-col" style="left:5px"><h4>Cash register<br>solutions</h4><ul><li>BC Retail</li><li>BC Photo</li><li>BC Jewellery</li><li>BC Wine &amp; Deli</li></ul></div>
    <div class="footer-col" style="left:182px"><h4>Entertainment</h4><ul><li>BC Entertainment</li><li>BC Ticketing</li><li>BC Member Card</li><li>BC AccessControl</li><li>BC Event Management</li></ul></div>
    <div class="footer-col" style="left:370px"><h4>Webshops</h4><ul><li>Webshop B2B</li><li>Webshop B2C</li></ul></div>
    <div class="footer-col compact" style="left:533px"><h4>Additional solutions</h4><ul><li>Collection Management</li><li>Campaign Tracker</li><li>Document Capture</li><li>QuarryReports</li><li>BC Loyalty</li><li>BC PDF-2-KEX</li><li>BC Brindle Docs</li><li>BC OIOUBL</li><li>BC SMS</li><li>Payment Management</li></ul></div>
    <div class="footer-col" style="left:808px"><h4>Contact us</h4><ul><li>Kontaktinfo</li><li>Ledige stillinger</li><li>About us</li></ul></div>
    <div class="badge" style="top:200px;background:var(--brand-deep)"></div>
    <div class="badge" style="top:272px;background:#24579a"></div>
  </footer>
</div>
</body>
</html>
```